Brand new letterhead, business card, email signature etc.

We are a financial company in London, UK. Our website is www.marlowvane.com. We're wanting a complete remodel of the company colours, letter head, business cards, email signatures, etc. Looking to keep the same font for the company name. I have upload a colour palette that we want to work with. We're looking for company letterhead for outgoing letters/ correspondence, letterhead for internal documentation, email signatures, e-letters. etc. Ultimately we will redesign the entire website also. It is important that our clients get a strong, secure, warm, trustworthy, solid feeling and first impression.
Updates

Designs look the same

Target Market(s)

Institutional investors, (ultra) high net worth individuals

Industry/Entity Type

Finance, Invesments banking.

Font styles to use
Other font styles liked:
• Current font is "Champagne & Limousines"

Requirements
Must have
• Must use the colours provided on the PDF uploaded to the portal. The purple = main colour. The red = accent colour.
Nice to have
• Nice to use same font as now for the company name "Corvane". Font is "Champagne & Limousines". Nice to have some reference to the old logo flower, but only subtle.
Should not have
• Do not use the colour red from our website. Use the colours provided on the colour palette PDF that I uploaded in the portal.

```html
<!DOCTYPE html>
<html lang="en">
<head>
<meta charset="utf-8">
<title>Corvane Stationery Suite</title>
<link rel="stylesheet" href="https://fonts.googleapis.com/css2?family=Josefin+Sans:wght@300;400&family=Quicksand:wght@500;600&display=swap">
<style>
  :root {
    --stage: #c8c7bf;
    --paper: #ffffff;
    --accent: #e03826;
    --plum: #2e0e1c;
    --ink: #2b2b2b;
    --ink-soft: #4a4a4a;
    --rule: #d9d6cc;
    --sand: #e0d9cf;
    --label: #3d3d3d;
  }
  * { box-sizing: border-box; margin: 0; padding: 0; }
  html, body { width: 1112px; height: 1200px; overflow: hidden; }
  body {
    position: relative;
    background: var(--stage);
    font-family: "Josefin Sans", sans-serif;
    color: var(--ink);
  }

  .piece {
    position: absolute;
    background: var(--paper);
    box-shadow: 0 2px 5px rgba(0,0,0,0.18);
    overflow: hidden;
  }
  .band { position: absolute; left: 0; top: 0; width: 100%; background: var(--accent); }

  .piece-label {
    position: absolute;
    font-family: "Josefin Sans", sans-serif;
    font-weight: 300;
    font-size: 10px;
    color: var(--label);
    text-align: right;
  }

  /* contact block */
  .contact {
    position: absolute;
    top: 0;
    font-weight: 300;
    color: var(--ink-soft);
  }
  .contact-row {
    display: flex;
    align-items: stretch;
  }
  .contact-text {
    width: var(--text-w);
    margin-right: 0.7em;
    text-align: right;
    line-height: 1.1;
    display: flex;
    flex-direction: column;
    justify-content: flex-end;
    padding-bottom: 0.35em;
  }
  .contact-row + .contact-row .contact-text { border-top: 1px solid var(--rule); padding-top: 0.4em; }
  .contact-icon {
    width: 2.78em;
    background: var(--plum);
    display: flex;
    align-items: flex-end;
    justify-content: center;
    padding-bottom: 0.55em;
  }
  .contact-row + .contact-row .contact-icon { border-top: 1px solid #4a2a38; }
  .contact-icon svg { width: 1.5em; height: 1.5em; display: block; }
  .row-phone .contact-text, .row-phone .contact-icon { padding-top: var(--lead); }
  .row-web, .row-web > * { min-height: 3.06em; }
  .row-address, .row-address > * { min-height: 2.9em; }

  /* wordmark */
  .wordmark {
    position: absolute;
    display: flex;
    align-items: center;
  }
  .wordmark-square {
    border: 1px solid var(--ink);
    background: var(--paper);
    flex: none;
  }
  .wordmark-name {
    font-family: "Josefin Sans", sans-serif;
    font-weight: 300;
    color: var(--ink);
    letter-spacing: 0.18em;
    line-height: 1;
  }

  /* person */
  .person { position: absolute; }
  .person-name {
    font-family: "Quicksand", sans-serif;
    font-weight: 600;
    font-size: 11.5px;
    color: var(--plum);
    line-height: 1;
  }
  .person-role {
    font-family: "Quicksand", sans-serif;
    font-weight: 600;
    font-size: 6.5px;
    color: var(--plum);
    line-height: 1.1;
  }

  /* letterhead */
  .letterhead { left: 87px; top: 78px; width: 762px; height: 1032px; box-shadow: 0 10px 14px -6px rgba(0,0,0,0.35); }
  .letterhead .band { height: 33px; }
  .letterhead .contact { right: 35px; font-size: 14.4px; --text-w: 12em; --lead: 5.9em; }
  .letterhead .wordmark { left: 58px; top: 91px; gap: 12px; }
  .letterhead .wordmark-square { width: 51px; height: 51px; }
  .letterhead .wordmark-name { font-size: 31px; }

  /* business cards */
  .card { width: 329px; height: 188px; }
  .card-front { left: 691px; top: 426px; }
  .card-front .band, .signature .band { height: 14px; }
  .card .contact, .signature .contact { font-size: 7.9px; --text-w: 12.3em; --lead: 3.4em; }
  .card-front .contact { right: 17px; }
  .card-front .person { left: 17px; top: 31px; }
  .card-front .wordmark, .signature .wordmark { gap: 7px; }
  .card-front .wordmark { left: 17px; top: 142px; }
  .card .wordmark-square, .signature .wordmark-square { width: 29px; height: 29px; }
  .card .wordmark-name, .signature .wordmark-name { font-size: 16.5px; }

  .card-back { left: 692px; top: 646px; background: var(--sand); }
  .card-back .mark-panel {
    position: absolute; left: 109px; top: 30px; width: 109px; height: 109px;
    background: var(--paper); padding: 4px;
  }
  .card-back .mark-panel span { display: block; width: 100%; height: 100%; border: 1.5px solid var(--ink); }
  .card-back .site {
    position: absolute; left: 0; width: 100%; top: 150px;
    text-align: center; font-size: 9px; letter-spacing: 0.42em; color: var(--ink);
    font-weight: 400;
  }

  /* email signature */
  .signature { left: 508px; top: 871px; width: 517px; height: 188px; }
  .signature .contact { right: 18px; }
  .signature .portrait {
    position: absolute; left: 0; top: 14px; width: 142px; height: 174px;
    background: linear-gradient(160deg, #c9d0d6 0%, #8c98a4 45%, #1f2b45 75%, #16203a 100%);
  }
  .signature .person { left: 156px; top: 32px; }
  .signature .wordmark { left: 156px; top: 134px; }
</style>
</head>
<body>

  <!-- Letterhead -->
  <section class="piece letterhead">
    <div class="band"></div>
    <div class="wordmark">
      <span class="wordmark-square"></span>
      <span class="wordmark-name">CORVANE</span>
    </div>
    <div class="contact">
      <div class="contact-row row-phone">
        <div class="contact-text"><span>+000 12345 6789</span><span>+000 12345 6789</span></div>
        <div class="contact-icon"><svg viewBox="0 0 24 24" fill="#fff"><path d="M3 9c0-2 4-4 9-4s9 2 9 4v2h-4V9c-1-.6-3-1-5-1s-4 .4-5 1v2H3z"/><path d="M6 12l2-3h8l2 3v6H6z"/><rect x="9" y="12" width="6" height="4" fill="#2e0e1c"/></svg></div>
      </div>
      <div class="contact-row row-web">
        <div class="contact-text"><span>urwebsitename.com</span><span>urname@email.com</span></div>
        <div class="contact-icon"><svg viewBox="0 0 24 24" fill="none" stroke="#fff" stroke-width="1.6"><circle cx="12" cy="12" r="8.5"/><path d="M5 8c4 1 6 4 6 8M9 4c3 3 8 4 11 3M4.5 15c4-1 9 0 13 4"/></svg></div>
      </div>
      <div class="contact-row row-address">
        <div class="contact-text"><span>1234 Street name, town/city,</span><span>state/country, post/zip 012345.</span></div>
        <div class="contact-icon"><svg viewBox="0 0 24 24" fill="#fff"><path d="M12 2a7 7 0 0 0-7 7c0 5 7 13 7 13s7-8 7-13a7 7 0 0 0-7-7zm0 9.5a2.5 2.5 0 1 1 0-5 2.5 2.5 0 0 1 0 5z"/></svg></div>
      </div>
    </div>
  </section>

  <!-- Business card front -->
  <p class="piece-label" style="right:92px; top:406px;">Business card front</p>
  <section class="piece card card-front">
    <div class="band"></div>
    <div class="person">
      <p class="person-name">Julian Hartley</p>
      <p class="person-role">Designation</p>
    </div>
    <div class="contact">
      <div class="contact-row row-phone">
        <div class="contact-text"><span>+000 12345 6789</span><span>+000 12345 6789</span></div>
        <div class="contact-icon"><svg viewBox="0 0 24 24" fill="#fff"><path d="M3 9c0-2 4-4 9-4s9 2 9 4v2h-4V9c-1-.6-3-1-5-1s-4 .4-5 1v2H3z"/><path d="M6 12l2-3h8l2 3v6H6z"/><rect x="9" y="12" width="6" height="4" fill="#2e0e1c"/></svg></div>
      </div>
      <div class="contact-row row-web">
        <div class="contact-text"><span>urwebsitename.com</span><span>urname@email.com</span></div>
        <div class="contact-icon"><svg viewBox="0 0 24 24" fill="none" stroke="#fff" stroke-width="1.8"><circle cx="12" cy="12" r="8.5"/><path d="M5 8c4 1 6 4 6 8M9 4c3 3 8 4 11 3M4.5 15c4-1 9 0 13 4"/></svg></div>
      </div>
      <div class="contact-row row-address">
        <div class="contact-text"><span>1234 Street name, town/city,</span><span>state/country, post/zip 012345.</span></div>
        <div class="contact-icon"><svg viewBox="0 0 24 24" fill="#fff"><path d="M12 2a7 7 0 0 0-7 7c0 5 7 13 7 13s7-8 7-13a7 7 0 0 0-7-7zm0 9.5a2.5 2.5 0 1 1 0-5 2.5 2.5 0 0 1 0 5z"/></svg></div>
      </div>
    </div>
    <div class="wordmark">
      <span class="wordmark-square"></span>
      <span class="wordmark-name">CORVANE</span>
    </div>
  </section>

  <!-- Business card back -->
  <p class="piece-label" style="right:88px; top:630px;">Business card back</p>
  <section class="piece card card-back">
    <div class="mark-panel"><span></span></div>
    <p class="site">www.marlowvane.com</p>
  </section>

  <!-- Email signature -->
  <p class="piece-label" style="right:85px; top:858px;">Email Signature</p>
  <section class="piece signature">
    <div class="band"></div>
    <div class="portrait" role="img" aria-label="Portrait photograph of the team member in a dark suit"></div>
    <div class="person">
      <p class="person-name">Julian Hartley</p>
      <p class="person-role">Designation</p>
    </div>
    <div class="contact">
      <div class="contact-row row-phone">
        <div class="contact-text"><span>+000 12345 6789</span><span>+000 12345 6789</span></div>
        <div class="contact-icon"><svg viewBox="0 0 24 24" fill="#fff"><path d="M3 9c0-2 4-4 9-4s9 2 9 4v2h-4V9c-1-.6-3-1-5-1s-4 .4-5 1v2H3z"/><path d="M6 12l2-3h8l2 3v6H6z"/><rect x="9" y="12" width="6" height="4" fill="#2e0e1c"/></svg></div>
      </div>
      <div class="contact-row row-web">
        <div class="contact-text"><span>urwebsitename.com</span><span>urname@email.com</span></div>
        <div class="contact-icon"><svg viewBox="0 0 24 24" fill="none" stroke="#fff" stroke-width="1.8"><circle cx="12" cy="12" r="8.5"/><path d="M5 8c4 1 6 4 6 8M9 4c3 3 8 4 11 3M4.5 15c4-1 9 0 13 4"/></svg></div>
      </div>
      <div class="contact-row row-address">
        <div class="contact-text"><span>1234 Street name, town/city,</span><span>state/country, post/zip 012345.</span></div>
        <div class="contact-icon"><svg viewBox="0 0 24 24" fill="#fff"><path d="M12 2a7 7 0 0 0-7 7c0 5 7 13 7 13s7-8 7-13a7 7 0 0 0-7-7zm0 9.5a2.5 2.5 0 1 1 0-5 2.5 2.5 0 0 1 0 5z"/></svg></div>
      </div>
    </div>
    <div class="wordmark">
      <span class="wordmark-square"></span>
      <span class="wordmark-name">CORVANE</span>
    </div>
  </section>

</body>
</html>
```